Kinesiology undergraduate program needs an infographic

We would like an infographic to creatively and succinctly inform students, faculty, staff, and others about our undergraduate values and competencies (perhaps also integrating our mission and vision). We would like to see a design that incorporates the definition of Kinesiology (the study of human movement) and the colors of our Westbrook State University at Harlan.

```html
<!DOCTYPE html>
<html lang="en">
<head>
<meta charset="UTF-8">
<title>Kinesiology Undergraduate Program – Mission, Vision and Values</title>
<link href="https://fonts.googleapis.com/css2?family=Archivo+Black&family=Poppins:wght@400;700&display=swap" rel="stylesheet">
<style>
  :root {
    --brand-red: #e30a17;
    --brand-salmon: #f0745e;
    --navy: #1f1b4d;
    --ink: #2b2b2b;
    --band-grey: #efefef;
    --disc-grey: #ececec;
    --floor-grey: #e3e3e3;
    --white: #ffffff;
  }
  * { margin: 0; padding: 0; box-sizing: border-box; }
  html, body { width: 1200px; height: 848px; overflow: hidden; background: var(--white); }
  body { position: relative; font-family: "Poppins", sans-serif; color: var(--ink); }

  .top-band { position: absolute; left: 0; top: 0; width: 1200px; height: 107px; background: var(--brand-red); }
  .sub-band { position: absolute; left: 0; top: 107px; width: 1200px; height: 24px; background: var(--band-grey); }

  .college-badge {
    position: absolute; left: 45px; top: 18px; width: 140px; height: 140px;
    background: var(--white); box-shadow: 4px 6px 10px rgba(0,0,0,.35);
    padding: 24px 0 0 16px;
    font-family: "Poppins", sans-serif; font-weight: 700; font-size: 12px; line-height: 13px; text-transform: uppercase;
  }
  .college-badge .dept { color: var(--brand-red); }
  .college-badge .college { color: var(--brand-salmon); }
  .college-badge .uni-name { margin-top: 3px; color: var(--brand-red); }

  .heading {
    position: absolute; font-family: "Archivo Black", sans-serif; color: var(--brand-red);
    font-size: 42px; line-height: 1; letter-spacing: 0; text-transform: uppercase; font-weight: 400;
  }
  .body-text { position: absolute; font-size: 16.4px; line-height: 20.6px; color: var(--ink); }

  .stage-disc { position: absolute; left: 405px; top: 300px; width: 392px; height: 392px; border-radius: 50%; background: var(--disc-grey); }
  .floor-shadow { position: absolute; left: 455px; top: 765px; width: 215px; height: 48px; border-radius: 50%; background: var(--floor-grey); }
  .figure {
    position: absolute; left: 470px; top: 222px; width: 270px; height: 590px; border-radius: 60px 60px 30px 30px;
    background: linear-gradient(90deg, #e32a2a 0%, #c41e24 30%, #2a2a2a 48%, #c98a6c 52%, #b9533f 75%, #e3b495 100%);
    opacity: .9;
  }
  .divider { position: absolute; left: 598px; top: 220px; width: 6px; height: 608px; background: var(--navy); }

  .connectors { position: absolute; left: 0; top: 0; }

  .competency { position: absolute; }
  .competency h3 {
    font-family: "Archivo Black", sans-serif; font-size: 15.5px; line-height: 20px; color: var(--navy);
    text-transform: uppercase; letter-spacing: .4px; font-weight: 400;
  }
  .competency li { list-style: none; font-size: 16.6px; line-height: 20.5px; }

  .icon { position: absolute; }
</style>
</head>
<body>
  <div class="top-band"></div>
  <div class="sub-band"></div>

  <div class="college-badge">
    <div class="dept">Kinesiology<br>and Wellness</div>
    <div class="college">School of<br>Human Health<br>Sciences</div>
    <div class="uni-name">WSUH</div>
  </div>

  <div class="stage-disc"></div>
  <div class="floor-shadow"></div>
  <div class="figure" role="img" aria-label="Illustration of a student in a red hoodie with backpack, split down the middle to show the human muscular anatomy"></div>
  <div class="divider"></div>

  <h1 class="heading" style="left:93px; top:205px;">Our Mission</h1>
  <p class="body-text" style="left:88px; top:247px; width:340px;">To empower undergraduate students<br>to pursue excellence through<br>scientific discovery, clinical practice,<br>and health promotion</p>

  <h2 class="heading" style="left:774px; top:177px;">Our Vision</h2>
  <p class="body-text" style="left:774px; top:217px; width:400px;">WSUH Kinesiology graduates are leaders who<br>excel in careers that enhance the quality of<br>life of individuals and communities</p>

  <h2 class="heading" style="left:774px; top:309px;">Our Values</h2>
  <p class="body-text" style="left:774px; top:349px; width:400px;">Student Success, Science, and Service<br>Our Graduates Will Be Competent In...</p>

  <svg class="connectors" width="1200" height="848" viewBox="0 0 1200 848" aria-hidden="true">
    <g fill="none" stroke="#111" stroke-width="1.5">
      <polyline points="355,398 207,398 207,482"/>
      <polyline points="413,611 387,611 387,667 310,667"/>
      <polyline points="785,428 805,428 805,497 828,497"/>
      <polyline points="746,573 800,573 800,663 843,663"/>
    </g>
    <g fill="#111">
      <circle cx="355" cy="398" r="5.5"/><circle cx="207" cy="482" r="5.5"/>
      <circle cx="413" cy="611" r="5.5"/><circle cx="310" cy="667" r="5.5"/>
      <circle cx="785" cy="428" r="5.5"/><circle cx="828" cy="497" r="5.5"/>
      <circle cx="746" cy="573" r="5.5"/><circle cx="843" cy="663" r="5.5"/>
    </g>
  </svg>

  <svg class="icon" style="left:110px; top:418px;" width="60" height="60" viewBox="0 0 60 60" aria-hidden="true">
    <g fill="none" stroke="#1f1b4d" stroke-width="3" stroke-linejoin="round">
      <path d="M8 14 L14 8 L54 48 L56 56 L48 54 Z"/>
      <line x1="12" y1="20" x2="20" y2="12"/>
      <line x1="44" y1="52" x2="52" y2="44"/>
    </g>
  </svg>

  <svg class="icon" style="left:40px; top:628px;" width="72" height="72" viewBox="0 0 72 72" aria-hidden="true">
    <g fill="none" stroke="#1f1b4d" stroke-width="3">
      <ellipse cx="36" cy="36" rx="33" ry="12"/>
      <ellipse cx="36" cy="36" rx="33" ry="12" transform="rotate(60 36 36)"/>
      <ellipse cx="36" cy="36" rx="33" ry="12" transform="rotate(-60 36 36)"/>
    </g>
    <circle cx="36" cy="36" r="5" fill="#1f1b4d"/>
  </svg>

  <svg class="icon" style="left:1090px; top:438px;" width="78" height="82" viewBox="0 0 78 82" aria-hidden="true">
    <g fill="none" stroke="#1f1b4d" stroke-width="3" stroke-linecap="round">
      <path d="M28 56 C28 46 20 42 20 32 A19 19 0 0 1 58 32 C58 42 50 46 50 56 Z"/>
      <line x1="29" y1="63" x2="49" y2="63"/><line x1="31" y1="70" x2="47" y2="70"/>
      <path d="M33 77 H45"/>
      <line x1="39" y1="2" x2="39" y2="7"/>
      <line x1="6" y1="32" x2="11" y2="32"/><line x1="67" y1="32" x2="72" y2="32"/>
      <line x1="14" y1="10" x2="18" y2="14"/><line x1="64" y1="10" x2="60" y2="14"/>
      <line x1="10" y1="50" x2="15" y2="47"/><line x1="68" y1="50" x2="63" y2="47"/>
    </g>
  </svg>

  <svg class="icon" style="left:1068px; top:628px;" width="80" height="80" viewBox="0 0 80 80" aria-hidden="true">
    <g fill="none" stroke="#1f1b4d" stroke-width="3">
      <circle cx="40" cy="40" r="36"/>
      <circle cx="40" cy="40" r="26"/>
      <circle cx="40" cy="40" r="9"/>
      <path d="M40 20 L44 31 L56 30 L48 39 L56 49 L44 48 L40 60 L36 48 L24 49 L32 39 L24 30 L36 31 Z"/>
    </g>
  </svg>

  <section class="competency" style="left:123px; top:493px;">
    <h3>Intrapersonal Growth</h3>
    <ul>
      <li>Cultural Humility/Sensitivity</li>
      <li>Integrity</li>
      <li>Self-Directed</li>
      <li>Dependability</li>
      <li>Mission Oriented</li>
    </ul>
  </section>

  <section class="competency" style="left:123px; top:653px;">
    <h3>The Science of<br>Kinesiology</h3>
    <ul>
      <li>Foundational Concepts of<br>Kinesiology</li>
      <li>Clinical Application</li>
      <li>Scientific Communication</li>
    </ul>
  </section>

  <section class="competency" style="left:860px; top:493px;">
    <h3>Thinking and Reasoning</h3>
    <ul>
      <li>Critical Thinking</li>
      <li>Quantitative Reasoning</li>
      <li>Scientific Inquiry</li>
      <li>Concept Integration</li>
    </ul>
  </section>

  <section class="competency" style="left:860px; top:653px;">
    <h3>Relationships and<br>Communication</h3>
    <ul>
      <li>Cultural Competence</li>
      <li>Professionalism</li>
      <li>Leadership and Teamwork</li>
      <li>Service<br>Orientation/Citizenship</li>
    </ul>
  </section>
</body>
</html>
```